Luxury Tours Design

We are “Amber Coachline” a Chauffeur Company based in Maidenhead, Berkshire. Our website is - ambercoachline.co.uk which will give you an insite into the Company.
Our clients consist of luxurious Hotels, large Corporate Companies along with private UHNW clients.
We have a fleet of Valtrane E, S and V Class vehicles along with 16 Seater Executive Coaches so we can accommodate single travellers, couples, friends, families and groups.
We would like an A5 (or slightly larger) double sided colour leaflet designed to promote our Tours in our local and surrounding areas.
The information below is some indication as to what we would like.
On the front we would like:-
Amber Coachline “Signature Tour” This will be our main promoting Tour
Slogan “Amber Coachline….ever at your service”
Tour will include:-
Visiting the historic town of Windsor, Hollenby Castle, St Aldric’s Chapel and Regal Pemberly Shopping Arcade.
Then onto Eton (Dunmere College) and a lovely view of the River Thames along with an array of Antique Shops in the quaint streets.
Bray Village (Heron Isle), renowed for it’s Brevard Star Restaurants and pubs.
Through picturesque Cookham along to Marlow for some shopping in the boutique shops, small listed buildings and beautiful places for refreshments, along with stunning views of the River Thames form Ashcombe Bridge.
This will be our main tour we offer but again this is flexible. This aims to be around 4-5 hours.
On the front, a picture of Hollenby castle maybe a large picture with writing over the top, or a separate photo….. a couple of photos attached or something similar.
On the back of the leaflet:-
We offer London based tours including:-
Belvards, Larkmoor Park, Ravensholt Palace, Corringdale Palace, Pellington Square, Turning of the Sentries, Keep of Ardmoor, Tall Tom, Glenmoreton Abbey to name a few! Or maybe London by night with a show or restaurant.
On the back a picture of Corringdale Palace…a couple of picture are also attached or again something similar.
Other Tours provided:-
Ridgewell Court Palace, Oxford and Corvane Palace, Ashmarrow Ring and Bath, The Cotswolds, Stratford and Penlow Castle, Quillford Shopping Village.
Also bespoke Tours can be arranged. We can personalise any tour to your requirements.
Experienced friendly Chauffeur’s, no request too big or small.
Please call us on 01632 960417 or email us sales@ambercoachline.co.uk
Please can you do an initial design including the above information.
Look forward to hearing from you.
Kind regards
Please visit https://www.hartleyprivatedrives.co.uk/ to get an idea of the tours of London to go on the back.
Prices will follow to be added after design and layout has been done.
Our AC logo is available on www.ambercoachline.co.uk
We want text to be editable and also for the design to have a luxury feel.
Chauffeur

```html
<!DOCTYPE html>
<html lang="en">
<head>
<meta charset="utf-8">
<title>Amber Coachline – Tours Leaflet</title>
<link rel="stylesheet" href="https://fonts.googleapis.com/css2?family=Great+Vibes&family=Poppins:ital,wght@0,400;0,500;0,600;1,400;1,600&display=swap">
<style>
:root{
  --paper:#ffffff;
  --ink-dark:#2a2a25;
  --title-olive:#4a4430;
  --panel:rgba(104,96,66,0.82);
  --gold:#d6bd5c;
  --gold-deep:#8d7c38;
  --text-light:#ffffff;
  --text-dark:#2e2e2e;
}
*{margin:0;padding:0;box-sizing:border-box}
html,body{width:1200px;height:2400px;overflow:hidden;background:var(--paper)}
body{position:relative;font-family:"Poppins",sans-serif}
.leaflet{position:absolute;left:221px;width:758px;height:1076px;background:var(--ink-dark);overflow:hidden;box-shadow:0 6px 18px rgba(0,0,0,.35)}
.leaflet--front{top:98px}
.leaflet--back{top:1240px}
.photo{position:absolute;left:0;top:0;width:100%}
.photo--castle{height:620px;background:linear-gradient(180deg,#c9d3dc 0%,#e8c8c0 18%,#f1a894 26%,#b9ad9b 32%,#5f7d3e 42%,#3f6328 62%,#353d28 82%,var(--ink-dark) 100%)}
.photo--palace{height:660px;background:linear-gradient(180deg,#bcc8d6 0%,#dcd6da 24%,#f2b6a2 34%,#f0c9a4 42%,#d9d6cf 50%,#b9b6ad 62%,#d8c23a 70%,#c93a2c 80%,#6d7e2c 90%,var(--ink-dark) 100%)}
.script{font-family:"Great Vibes",cursive;font-weight:400;text-align:center;position:absolute;left:0;width:100%}
.front-title{top:30px;font-size:94px;color:var(--title-olive);line-height:1}
.front-slogan{top:140px;font-size:44px;color:var(--title-olive);line-height:1}
.fleet-intro{position:absolute;top:492px;left:60px;width:638px;text-align:center;color:var(--text-light);font-size:18px;font-weight:500;line-height:22px}
.tour-panel{position:absolute;left:89px;top:593px;width:581px;height:326px;background:var(--panel);padding:8px 22px 0}
.tour-heading{color:var(--gold);font-size:25px;font-weight:500;line-height:25px;text-transform:uppercase;margin-top:2px}
.price-tag{position:absolute;right:0;top:0;width:91px;height:31px;background:var(--gold-deep);color:var(--text-light);padding:2px 0 0 12px}
.price-tag small{display:block;font-size:6px;line-height:6px}
.price-tag strong{display:block;font-size:17px;font-weight:600;line-height:20px}
.tour-stops{margin-top:22px;list-style:none}
.tour-stops li{color:var(--text-light);font-size:13px;line-height:15px;margin-bottom:15px;width:530px}
.tour-quote{color:var(--gold);font-style:italic;font-size:17px;text-align:center;margin-top:-2px}
.tour-quote b,.bespoke b{font-style:normal;font-family:Georgia,serif;font-size:26px;vertical-align:-4px}
.contact-bar{position:absolute;top:960px;left:0;width:100%;display:flex;justify-content:center;align-items:center;gap:0;color:var(--text-light);font-size:13px;font-weight:500}
.contact-bar .sep{width:1px;height:14px;background:var(--gold-deep);margin:0 22px}
.contact-bar .phone{font-size:15px}
.contact-item{display:flex;align-items:center;gap:7px}
.contact-item svg{width:16px;height:16px}
.brand{position:absolute;top:1010px;left:0;width:100%;display:flex;justify-content:center;align-items:center;gap:8px;color:var(--text-light);font-size:21px;font-weight:400}
.brand-mark{width:32px;height:32px;border-radius:50%;background:#8c8a84}
.back-title{top:28px;font-size:84px;color:#1f1f1f;line-height:1}
.sights{position:absolute;top:120px;left:68px;width:660px;display:flex}
.sights ul{list-style:none;color:var(--text-dark);font-size:17px;line-height:29px}
.sights ul:nth-child(1){width:205px}
.sights ul:nth-child(2){width:257px}
.sights ul:nth-child(3){margin-top:-4px}
.night-note{position:absolute;top:226px;left:68px;font-size:17px;font-style:italic;font-weight:600;color:#1f1f1f}
.other-panel{position:absolute;left:73px;top:633px;width:611px;height:281px;background:var(--panel)}
.other-title{top:12px;font-size:54px;color:var(--gold);line-height:1}
.other-tours{position:absolute;top:92px;left:47px;display:flex}
.other-tours ul{list-style:none;color:var(--text-light);font-size:14px;line-height:29px;text-transform:uppercase}
.other-tours ul:first-child{width:281px}
.bespoke{position:absolute;top:205px;left:0;width:100%;text-align:center;color:var(--gold);font-style:italic;font-size:15px;line-height:18px}
.prices{position:absolute;top:253px;left:0;width:100%;text-align:center;color:var(--gold);font-size:17px}
</style>
</head>
<body>

<section class="leaflet leaflet--front">
  <div class="photo photo--castle" role="img" aria-label="Hollenby Castle at the end of a long tree-lined avenue under a pink dusk sky"></div>
  <h1 class="script front-title">Signature Tour</h1>
  <p class="script front-slogan">Amber Coachline..Ever at your service..</p>
  <p class="fleet-intro">We have a fleet of Valtrane E, S and V Class vehicles along with 16 Seater Executive Coaches so we can accommodate single travellers, couples, friends, families and groups.</p>

  <article class="tour-panel">
    <h2 class="tour-heading">Visit to the historic<br>town of Windsor</h2>
    <div class="price-tag"><small>FROM</small><strong>£350.00</strong></div>
    <ul class="tour-stops">
      <li>Visiting the historic town of Windsor, Hollenby Castle, St Aldric’s Chapel and Regal Pemberly Shopping Arcade.</li>
      <li>Eton and Dunmere College with lovely views of the River Thames along with an array of Antique Shops in the quaint streets.</li>
      <li>Bray Village renowned for it's Brevard Star restaurants and pubs, along with a visit to Heron Isle.</li>
      <li>Through picturesque Cookham along to Marlow for some shopping in the boutique shops, small listed buildings and beautiful places for refreshments, along with stunning views of the River Thames from Ashcombe Bridge.</li>
    </ul>
    <p class="tour-quote"><b>“</b>Our signature tour is approximately 4 hours<b>”</b></p>
  </article>

  <div class="contact-bar">
    <span class="contact-item"><svg viewBox="0 0 16 16"><circle cx="8" cy="8" r="7.2" fill="none" stroke="#d6bd5c"/><rect x="4.3" y="5.3" width="7.4" height="5.4" fill="none" stroke="#d6bd5c" stroke-width=".9"/><path d="M4.3 5.3 8 8.3 11.7 5.3" fill="none" stroke="#d6bd5c" stroke-width=".9"/></svg>sales@ambercoachline.co.uk</span>
    <span class="sep"></span>
    <span class="contact-item phone"><svg viewBox="0 0 16 16"><circle cx="8" cy="8" r="7.2" fill="none" stroke="#d6bd5c"/><path d="M5.2 4.4l1.4-.2.8 1.9-.9.7c.5 1.1 1.3 1.9 2.4 2.4l.7-.9 1.9.8-.2 1.4c-3.5.2-6.3-2.6-6.1-6.1z" fill="none" stroke="#d6bd5c" stroke-width=".9"/></svg>01632 960417</span>
    <span class="sep"></span>
    <span class="contact-item"><svg viewBox="0 0 16 16"><circle cx="8" cy="8" r="7.2" fill="none" stroke="#d6bd5c"/><circle cx="8" cy="8" r="4" fill="none" stroke="#d6bd5c" stroke-width=".9"/><path d="M4 8h8M8 4c-1.6 2.2-1.6 5.8 0 8M8 4c1.6 2.2 1.6 5.8 0 8" fill="none" stroke="#d6bd5c" stroke-width=".8"/></svg>www.ambercoachline.co.uk</span>
  </div>
  <div class="brand"><span class="brand-mark"></span>Amber Coachline</div>
</section>

<section class="leaflet leaflet--back">
  <div class="photo photo--palace" role="img" aria-label="Corringdale Palace and a gilded memorial behind beds of red and yellow tulips"></div>
  <h1 class="script back-title">London Tours</h1>
  <div class="sights">
    <ul><li>Belvards</li><li>Larkmoor Park</li><li>Ravensholt Palace</li></ul>
    <ul><li>Corringdale Palace</li><li>Pellington Square</li><li>Turning of the Sentries</li></ul>
    <ul><li>Keep of Ardmoor</li><li>Tall Tom</li><li>Glenmoreton Abbey</li></ul>
  </div>
  <p class="night-note">Or maybe London by night with a show or restaurant.</p>

  <article class="other-panel">
    <h2 class="script other-title">Other Tours Available</h2>
    <div class="other-tours">
      <ul><li>Ridgewell Court Palace</li><li>Oxford and Corvane Palace</li><li>Ashmarrow Ring and Bath</li></ul>
      <ul><li>The Cotswolds</li><li>Stratford and Penlow Castle</li><li>Quillford Shopping Village</li></ul>
    </div>
    <p class="bespoke"><b>“</b> Also bespoke tours can be arranged. We can personalize any tour to <b>”</b><br>your requirements with our friendly, experienced chauffeurs</p>
    <p class="prices">Prices On Request</p>
  </article>

  <div class="contact-bar">
    <span class="contact-item"><svg viewBox="0 0 16 16"><circle cx="8" cy="8" r="7.2" fill="none" stroke="#d6bd5c"/><rect x="4.3" y="5.3" width="7.4" height="5.4" fill="none" stroke="#d6bd5c" stroke-width=".9"/><path d="M4.3 5.3 8 8.3 11.7 5.3" fill="none" stroke="#d6bd5c" stroke-width=".9"/></svg>sales@ambercoachline.co.uk</span>
    <span class="sep"></span>
    <span class="contact-item phone"><svg viewBox="0 0 16 16"><circle cx="8" cy="8" r="7.2" fill="none" stroke="#d6bd5c"/><path d="M5.2 4.4l1.4-.2.8 1.9-.9.7c.5 1.1 1.3 1.9 2.4 2.4l.7-.9 1.9.8-.2 1.4c-3.5.2-6.3-2.6-6.1-6.1z" fill="none" stroke="#d6bd5c" stroke-width=".9"/></svg>01632 960417</span>
    <span class="sep"></span>
    <span class="contact-item"><svg viewBox="0 0 16 16"><circle cx="8" cy="8" r="7.2" fill="none" stroke="#d6bd5c"/><circle cx="8" cy="8" r="4" fill="none" stroke="#d6bd5c" stroke-width=".9"/><path d="M4 8h8M8 4c-1.6 2.2-1.6 5.8 0 8M8 4c1.6 2.2 1.6 5.8 0 8" fill="none" stroke="#d6bd5c" stroke-width=".8"/></svg>www.ambercoachline.co.uk</span>
  </div>
  <div class="brand"><span class="brand-mark"></span>Amber Coachline</div>
</section>

</body>
</html>
```